Brimsett Gardening Fresh New Website

We are looking to create a simple fresh website for our landscaping business. The website should appeal to a 'high end' audience. We deal with a lot of Embassies and affluent clients who have extremely large gardens that are meticulously maintained. The site is about communicating our excellent landscaping and customer service skills and encouraging new clients to reach out and engage us to take care of their gardens.

The website is basically going to be our business card, it will have almost no functionality other than two 'contact us' forms, one for smaller clients and one for more detailed projects.

The website will not have a lot of written content and will have to show photos of beautifully landscaped gardens.

The main logo in black will influence the site, however, we are open to all suggestions.

We are expecting to have the following pages:
Home Page
Services
About Us
Contact Us
Showcase (photo gallery of our work)

We need someone who can code it to wordpress and be available for minor changes over a number of days. They will be simple tweaks.

```html
<!DOCTYPE html>
<html lang="en">
<head>
<meta charset="UTF-8">
<title>Brimsett Gardening</title>
<link href="https://fonts.googleapis.com/css2?family=PT+Serif:wght@400;700&family=Poppins:wght@400;500;600&display=swap" rel="stylesheet">
<style>
:root{
  --yellow:#f3b81f;
  --dark:#1b1b1b;
  --forest:#1f2b17;
  --field:#ececec;
  --text:#222;
  --white:#fff;
  --serif:'PT Serif', Georgia, serif;
  --sans:'Poppins', Arial, sans-serif;
}
*{box-sizing:border-box;margin:0;padding:0}
html,body{width:1200px;height:4065px;overflow:hidden}
body{position:relative;font-family:var(--sans);color:var(--text);background:var(--white)}

/* header */
.site-header{position:absolute;top:0;left:0;width:1200px;height:74px;background:var(--dark);z-index:5}
.main-nav{position:absolute;left:103px;top:28px;display:flex;gap:26px;font-size:14px;color:var(--white)}
.main-nav .active{color:var(--yellow)}
.brand-badge{position:absolute;left:535px;top:0;width:130px;height:145px;border-radius:0 0 65px 65px;background:var(--dark);z-index:6;text-align:center;padding-top:76px;font-family:var(--serif);font-size:14px;line-height:18px;color:var(--yellow)}
.call{position:absolute;left:726px;top:18px;display:flex;gap:12px;align-items:center;color:var(--white)}
.icon-circle{width:36px;height:36px;border-radius:50%;background:var(--yellow);display:flex;align-items:center;justify-content:center}
.call .label{font-family:var(--serif);font-weight:700;color:var(--yellow);font-size:17px;line-height:1.1}
.call .num{font-size:13px}
.btn{display:inline-block;background:var(--yellow);color:var(--dark);font-family:var(--serif);font-weight:700;border-radius:20px;text-align:center}
.login{position:absolute;left:970px;top:21px;width:107px;height:33px;line-height:33px;font-size:15px}

/* hero */
.hero{position:absolute;top:0;left:0;width:1200px;height:640px;background:linear-gradient(180deg,#4b6a2c 0%,#6e8f36 35%,#5c8a2a 65%,#3f6a1f 100%)}
.hero-title{position:absolute;left:104px;top:178px;font-family:var(--serif);font-weight:700;font-size:37px;line-height:44px;color:var(--white);width:460px}
.hero-copy{position:absolute;left:104px;top:272px;width:410px;font-family:var(--serif);font-size:15px;line-height:23px;color:var(--white)}
.hero-cta{position:absolute;left:104px;top:354px;width:139px;height:33px;line-height:33px;font-size:14px}
.request-card{position:absolute;left:807px;top:107px;width:305px;height:389px;background:var(--white);border-top:6px solid var(--yellow);border-radius:150px 150px 0 0/28px 28px 0 0;text-align:center}
.request-card h2{font-family:var(--serif);font-size:20px;margin-top:60px;margin-bottom:20px}
.pill{display:block;width:261px;height:33px;margin:0 auto 16px;border:1.5px solid #333;border-radius:18px;text-align:left;padding:8px 14px;font-size:11px;position:relative}
.pill .chev{position:absolute;right:14px;top:7px;font-size:11px}
.request-card .submit{width:139px;height:34px;line-height:34px;font-size:14px;margin-top:6px}

/* section headings */
.sec-title{position:absolute;left:0;width:1200px;text-align:center;font-family:var(--serif);font-weight:700;font-size:31px;color:var(--dark)}
.rule{position:absolute;left:572px;width:56px;height:3px;background:var(--yellow)}

/* services */
.service-card{position:absolute;width:262px;height:262px;border-radius:50%;overflow:hidden;background:var(--white);border:5px solid #fbeccb;box-shadow:0 6px 14px rgba(0,0,0,.12);text-align:center}
.service-card .photo{height:128px;width:100%}
.service-card h3{font-family:var(--serif);font-weight:700;font-size:19px;line-height:26px;margin-top:18px;height:52px;display:flex;align-items:center;justify-content:center}
.service-card .more{font-family:var(--serif);font-weight:700;font-size:14px;color:var(--yellow);text-decoration:underline;margin-top:6px;display:inline-flex;align-items:center;gap:4px}
.service-card.featured{background:var(--yellow)}
.service-card.featured .more{color:var(--dark)}

/* about */
.about{position:absolute;top:1492px;left:0;width:1200px;height:656px;background:linear-gradient(180deg,#1a2413 0%,#22301a 50%,#324a22 75%,#2b3f1d 100%)}
.about-frame{position:absolute;left:129px;top:139px;width:391px;height:363px;border:3px solid var(--yellow);border-radius:6px}
.about-photo{position:absolute;left:104px;top:122px;width:383px;height:355px;border-radius:6px;background:linear-gradient(135deg,#7b8a76,#9a8f7a 45%,#4e7030)}
.about-video{position:absolute;left:385px;top:354px;width:191px;height:177px;border-radius:6px;background:linear-gradient(160deg,#9aa59a,#5b7e3a 60%,#3b5a27)}
.play{position:absolute;left:80px;top:74px}
.about h2{position:absolute;left:641px;top:210px;font-family:var(--serif);font-weight:700;font-size:40px;color:var(--yellow)}
.about .bar{position:absolute;left:641px;top:262px;width:55px;height:3px;background:var(--yellow)}
.about p{position:absolute;left:641px;top:286px;width:450px;font-family:var(--serif);font-size:14px;line-height:23px;color:var(--white)}
.about .read{position:absolute;left:643px;top:403px;width:115px;height:33px;line-height:33px;font-size:14px}

/* contact */
.field{position:absolute;height:50px;background:var(--field);padding:14px 16px;font-size:15px;color:#333}
.contact-submit{position:absolute;left:543px;top:2727px;width:114px;height:32px;line-height:32px;font-size:14px}

/* work */
.work{position:absolute;top:2850px;left:0;width:1200px;height:750px;background:linear-gradient(180deg,#f4f5ef 0%,#e6ead9 40%,#d9e0c4 100%)}
.tile{position:absolute;border-radius:3px}

/* footer */
.site-footer{position:absolute;top:3600px;left:0;width:1200px;height:465px;background:var(--dark);color:var(--white)}
.footer-brand{position:absolute;left:100px;top:150px;font-family:var(--serif);color:var(--yellow);text-align:center;width:245px;font-size:30px;line-height:38px}
.footer-brand .ring{width:60px;height:60px;border-radius:50%;border:2px solid var(--yellow);margin:0 auto 18px}
.f-col{position:absolute;top:118px}
.f-col h4{font-family:var(--serif);font-weight:700;font-size:22px;color:var(--yellow);margin-bottom:12px}
.f-col ul{list-style:none;font-size:14px;line-height:29px}
.f-col ul .active{color:var(--yellow)}
.f-item{display:flex;align-items:center;gap:10px;font-family:var(--serif);font-weight:700;font-size:18px;margin-top:6px}
.f-item .icon-circle{width:26px;height:26px}
.f-text{font-size:12px;line-height:24px;margin-left:4px}
.news{width:245px;height:32px;border:1.5px solid var(--white);border-radius:18px;position:relative;padding:7px 14px;font-size:12px}
.news .go{position:absolute;right:3px;top:3px;width:24px;height:24px}
.socials{display:flex;gap:8px;margin-top:16px}
.socials span{width:22px;height:22px;border-radius:50%;background:var(--yellow)}
.f-rule{position:absolute;left:104px;top:404px;width:990px;height:1px;background:#777}
.copyright{position:absolute;top:428px;left:0;width:1200px;text-align:center;font-family:var(--serif);font-size:12px}
</style>
</head>
<body>

<section class="hero" role="img" aria-label="Gardener mowing a green lawn with a lawn mower, daisies in the foreground"></section>

<header class="site-header">
  <nav class="main-nav">
    <span class="active">Home</span><span>Services</span><span>About Us</span><span>Contact Us</span><span>Showcase</span>
  </nav>
  <div class="call">
    <div class="icon-circle"><svg width="16" height="16" viewBox="0 0 24 24"><path fill="#1b1b1b" d="M6.6 10.8a15 15 0 0 0 6.6 6.6l2.2-2.2c.3-.3.7-.4 1-.2 1.1.4 2.3.6 3.6.6.6 0 1 .4 1 1V20c0 .6-.4 1-1 1A17 17 0 0 1 3 4c0-.6.4-1 1-1h3.5c.6 0 1 .4 1 1 0 1.3.2 2.5.6 3.6.1.3 0 .7-.2 1z"/></svg></div>
    <div><div class="label">Call Us :</div><div class="num">+1 555 014 2290</div></div>
  </div>
  <span class="btn login">LOG IN</span>
</header>
<div class="brand-badge">Brimsett<br>Gardening</div>

<h1 class="hero-title">WELCOME TO BRIMSETT GARDENING</h1>
<p class="hero-copy">Lorem ipsum dolor sit amet, consectetur adipiscing elit, sed do eiusmod tempor incididunt ut labore et dolore magna aliqua.</p>
<span class="btn hero-cta">GET IN TOUCH</span>

<form class="request-card">
  <h2>Requset A Service</h2>
  <span class="pill">Name</span>
  <span class="pill">Email</span>
  <span class="pill">Phone Number</span>
  <span class="pill">Services<span class="chev">&#8964;</span></span>
  <span class="btn submit">SUBMIT</span>
</form>

<h2 class="sec-title" style="top:722px">OUR SERVICES</h2>
<div class="rule" style="top:767px"></div>

<div class="service-card" style="left:141px;top:821px"><div class="photo" role="img" aria-label="Laying fresh turf rolls" style="background:linear-gradient(180deg,#6a8d3c,#4d6e2a)"></div><h3>Lawn<br>Maintenance</h3><span class="more">Read More <svg width="12" height="12" viewBox="0 0 12 12"><circle cx="6" cy="6" r="6" fill="currentColor"/><path d="M4 6h4M6 4l2 2-2 2" stroke="#fff" stroke-width="1.4" fill="none"/></svg></span></div>
<div class="service-card" style="left:472px;top:821px"><div class="photo" role="img" aria-label="Gardener trimming hedges" style="background:linear-gradient(180deg,#5a8a2f,#3e6a22)"></div><h3>Shrub<br>Trimming</h3><span class="more">Read More <svg width="12" height="12" viewBox="0 0 12 12"><circle cx="6" cy="6" r="6" fill="currentColor"/><path d="M4 6h4M6 4l2 2-2 2" stroke="#fff" stroke-width="1.4" fill="none"/></svg></span></div>
<div class="service-card" style="left:805px;top:821px"><div class="photo" role="img" aria-label="Gardener spreading mulch in a flower bed" style="background:linear-gradient(180deg,#4f7a32,#6b5a3a)"></div><h3>Mulching</h3><span class="more">Read More <svg width="12" height="12" viewBox="0 0 12 12"><circle cx="6" cy="6" r="6" fill="currentColor"/><path d="M4 6h4M6 4l2 2-2 2" stroke="#fff" stroke-width="1.4" fill="none"/></svg></span></div>

<div class="service-card" style="left:141px;top:1121px"><div class="photo" role="img" aria-label="Gardeners pulling weeds among plants" style="background:linear-gradient(180deg,#4fa0a6,#5b7d3a)"></div><h3>Weed<br>Control</h3><span class="more">Read More <svg width="12" height="12" viewBox="0 0 12 12"><circle cx="6" cy="6" r="6" fill="currentColor"/><path d="M4 6h4M6 4l2 2-2 2" stroke="#fff" stroke-width="1.4" fill="none"/></svg></span></div>
<div class="service-card featured" style="left:472px;top:1121px"><div class="photo" role="img" aria-label="Gardener using a grass trimmer" style="background:linear-gradient(180deg,#3d4a36,#4f7d2e)"></div><h3>Fertilizer<br>Programs</h3><span class="more">Read More <svg width="12" height="12" viewBox="0 0 12 12"><circle cx="6" cy="6" r="6" fill="currentColor"/><path d="M4 6h4M6 4l2 2-2 2" stroke="#f3b81f" stroke-width="1.4" fill="none"/></svg></span></div>
<div class="service-card" style="left:805px;top:1121px"><div class="photo" role="img" aria-label="Gardener mowing a misty park lawn" style="background:linear-gradient(180deg,#5c7a4a,#9aa58e 60%,#4d7a2c)"></div><h3>All Garden<br>Services</h3><span class="more">Read More <svg width="12" height="12" viewBox="0 0 12 12"><circle cx="6" cy="6" r="6" fill="currentColor"/><path d="M4 6h4M6 4l2 2-2 2" stroke="#fff" stroke-width="1.4" fill="none"/></svg></span></div>

<section class="about">
  <div class="about-frame"></div>
  <div class="about-photo" role="img" aria-label="Worker laying turf beside a paved path"></div>
  <div class="about-video" role="img" aria-label="Video of a gardener planting turf">
    <svg class="play" width="26" height="26" viewBox="0 0 26 26"><circle cx="13" cy="13" r="11" fill="none" stroke="#fff" stroke-width="2"/><path d="M10 8l8 5-8 5z" fill="#fff"/></svg>
  </div>
  <h2>ABOUT US</h2>
  <div class="bar"></div>
  <p>Lorem ipsum dolor sit amet, consectetur adipiscing elit, sed do eiusmod tempor incididunt ut labore et dolore magna aliqua. Quis ipsum suspendisse ultrices gravida. Risus commodo viverra maecenas accumsan lacus vel facilisis.</p>
  <span class="btn read">READ MORE</span>
</section>

<h2 class="sec-title" style="top:2217px">CONTACT US</h2>
<div class="rule" style="top:2264px"></div>
<div class="field" style="left:169px;top:2318px;width:425px">First Name</div>
<div class="field" style="left:605px;top:2318px;width:426px">Last &nbsp;Name</div>
<div class="field" style="left:169px;top:2383px;width:425px">Email</div>
<div class="field" style="left:605px;top:2383px;width:426px">Phone Number</div>
<div class="field" style="left:169px;top:2446px;width:425px">Location</div>
<div class="field" style="left:605px;top:2446px;width:426px">Area Address</div>
<div class="field" style="left:169px;top:2514px;width:862px;height:176px">Message</div>
<span class="btn contact-submit">SUBMIT</span>

<section class="work">
  <h2 class="sec-title" style="top:115px">OUR WORK</h2>
  <div class="rule" style="top:165px"></div>
  <div class="tile" role="img" aria-label="Park with curving brick path and trees" style="left:104px;top:208px;width:324px;height:428px;background:linear-gradient(180deg,#cfe0f0 0%,#b9cfe0 30%,#5f8c3a 55%,#a86a5a 80%,#6e9a3a 100%)"></div>
  <div class="tile" role="img" aria-label="Gardener laying turf beside a gravel border" style="left:437px;top:208px;width:324px;height:207px;background:linear-gradient(160deg,#6a8a4a,#9a8a80 55%,#3f3a35)"></div>
  <div class="tile" role="img" aria-label="Worker trimming grass along a path" style="left:771px;top:208px;width:323px;height:207px;background:linear-gradient(160deg,#4a6a2e,#7aa63a 60%,#5a8a2a)"></div>
  <div class="tile" role="img" aria-label="Gardener planting turf near a wooden fence" style="left:437px;top:428px;width:324px;height:208px;background:linear-gradient(160deg,#4a3a2e,#5a7a3a 55%,#3e5a28)"></div>
  <div class="tile" role="img" aria-label="Gardeners planting young shrubs" style="left:771px;top:428px;width:323px;height:208px;background:linear-gradient(160deg,#6a8a3a,#8a7a5a 50%,#3f5a2a)"></div>
</section>

<footer class="site-footer">
  <div class="footer-brand"><div class="ring"></div>Brimsett<br>Gardening</div>
  <div class="f-col" style="left:422px">
    <h4>Quick Links</h4>
    <ul><li class="active">Home</li><li>Services</li><li>About Us</li><li>Contact Us</li><li>Showcase</li></ul>
  </div>
  <div class="f-col" style="left:606px">
    <h4>Contact Us</h4>
    <div class="f-item"><span class="icon-circle"><svg width="12" height="14" viewBox="0 0 12 16"><path fill="#1b1b1b" d="M6 0a6 6 0 0 0-6 6c0 4.5 6 10 6 10s6-5.5 6-10a6 6 0 0 0-6-6zm0 8.5A2.5 2.5 0 1 1 6 3.5a2.5 2.5 0 0 1 0 5z"/></svg></span>Address :</div>
    <div class="f-text">253,Lorem ipsum dolor sit<br>amet, consectetur adipiscing elit</div>
    <div class="f-item"><span class="icon-circle"><svg width="12" height="12" viewBox="0 0 24 24"><path fill="#1b1b1b" d="M6.6 10.8a15 15 0 0 0 6.6 6.6l2.2-2.2c.3-.3.7-.4 1-.2 1.1.4 2.3.6 3.6.6.6 0 1 .4 1 1V20c0 .6-.4 1-1 1A17 17 0 0 1 3 4c0-.6.4-1 1-1h3.5c.6 0 1 .4 1 1 0 1.3.2 2.5.6 3.6.1.3 0 .7-.2 1z"/></svg></span>Phone :</div>
    <div class="f-text">+1 555 014 2290</div>
    <div class="f-item"><span class="icon-circle"><svg width="12" height="10" viewBox="0 0 16 12"><rect width="16" height="12" rx="1" fill="#1b1b1b"/><path d="M1 1l7 5 7-5" stroke="#f3b81f" stroke-width="1.4" fill="none"/></svg></span>Email :</div>
    <div class="f-text">info@brimsettgardening.com</div>
  </div>
  <div class="f-col" style="left:849px">
    <h4>Newsletter</h4>
    <div class="news">Enter Email<span class="icon-circle go"><svg width="12" height="12" viewBox="0 0 24 24"><path fill="#1b1b1b" d="M2 21l21-9L2 3v7l15 2-15 2z"/></svg></span></div>
    <div class="socials"><span></span><span></span><span></span><span></span></div>
  </div>
  <div class="f-rule"></div>
  <p class="copyright">©Copyrights 2024 Brimsett Gardening | All Rights Reserved</p>
</footer>

</body>
</html>
```